July 2022 Industrial Manufacturer Product Expo Mexico City

We manufacture large screws and fastners for large Mining equipment, Trains, large ships, airplanes, wind turbines, and so on. We also do custom work base on the customer needs. No matter the size we can make it.
We have a Expo coming up with companies all over the world. We have to stand out we are a family own business so our customer service will be above and beyond anyone can provide. We do not have a sales force to push our products and services we provide one on one service.
Plus@!! I'm looking for anything that you designers can come up with if it was your company to put on a business card, plus i want to do a 1 or 2 sided pamphlet, and then a website. We make Speciality Bolts for large mining equipment these bolts can be 3 to 4 foot long!!! Plus fasteners, Nuts, washers, any, size, strengths, special materials, we offer more of a ono on one customer service, We are a small company, family own, but can fulfill any type of orders. We can also provide special time lines for emergency orders. "We keep the machines running we here at KRV don't believe in down time" We want to hear any slogan based on our company to stand out.
Thanks i really appreciate all your work and options that we have to pick on. Plus just a thought we could possibly want to entertain a experience Marketing internet help maybe a employment possibility. Thanks

I need 2 cards one in Spanish and English Like the steel back ground maybe send me in some bright red and blue writing Same with the Black cards Please remove the word Military The logo KRV maybe integrate a picture of a Bolt 🔩 Thank you

Still looking for I need 2 cards one in Spanish and English Like the steel back ground maybe send me in some bright red and blue writing Same with the Black cards try bright writing Please remove the word Military The logo KRV maybe integrate a picture of a Bolt 🔩 Plus will need the company to make a brochure and website next Thank you

Target Market(s)

Large Mining, Ship, Train, Green Energy, VELM, and Government equipment. Throughout the World

Industry/Entity Type

We can Custom Manufacture any type of Fastners for Mining equipment, Trains, Ships, Green energy, Governments, or military projects. wind turbines,

Contact Information for Business Card

I attached the name and contact info that's on a card, plus the Company Logo. Would like industrial looking background with Bright Colors that will stand out!! If we can insert somewhere maybe on back that we "Custom Manufacture Any Size or Quantity Fastners for Large Mining Equipment, Trains, Ships, Green Energy Equipment or Government Projects

Font styles to use
Other font styles liked:
• You Pick, has to be bold, colorful standout, Professional looking Beable to read it.

Colors

Designer to choose colors to be used in the design.

Requirements
Must have
• Need in Spanish and English TO STANDOUT FROM THE REST OF THE EXPO!! See Business card details, Rounded corners
Nice to have
• Can i see some of the darker cards with Bright Red and Blue letters I like to see the different type of card material, heavy thickness, plastic, transparent, Metal types, Bright Colors, I saw like Raised letters like on the logo.

```html
<!DOCTYPE html>
<html lang="es">
<head>
<meta charset="UTF-8">
<title>KRV Business Cards</title>
<link href="https://fonts.googleapis.com/css2?family=Poppins:wght@400;500;700&display=swap" rel="stylesheet">
<style>
  :root {
    --stage: #1b1c1e;
    --card: #111112;
    --text: #f2f2f2;
    --accent: #0a8fd8;
    --band-top: #0b2f9a;
    --band-bottom: #1565d8;
    --rule: #4a4a4c;
    --mark: #9aa0a8;
  }
  * { box-sizing: border-box; margin: 0; padding: 0; }
  html, body { width: 1200px; height: 900px; overflow: hidden; }
  body {
    background: var(--stage);
    font-family: "Poppins", sans-serif;
    color: var(--text);
    display: flex;
    flex-direction: column;
    align-items: center;
    justify-content: center;
    gap: 56px;
  }
  .card {
    position: relative;
    width: 580px;
    height: 332px;
    background: var(--card);
    border-radius: 10px;
    overflow: hidden;
    box-shadow: 0 18px 40px rgba(0,0,0,.55);
    display: flex;
    flex-direction: column;
    align-items: center;
    justify-content: center;
    text-align: center;
  }
  .card__band {
    position: absolute;
    left: 0; right: 0; bottom: 0;
    height: 12px;
    background: linear-gradient(180deg, var(--band-top), var(--band-bottom));
  }
  .brand {
    display: flex;
    align-items: center;
    gap: 16px;
    margin-bottom: 22px;
  }
  .brand__square {
    width: 22px; height: 22px;
    background: var(--accent);
  }
  .brand__name {
    font-weight: 500;
    font-size: 84px;
    line-height: 1;
    letter-spacing: 10px;
    color: var(--mark);
  }
  .tagline {
    font-size: 16px;
    line-height: 1.3;
    font-weight: 400;
    max-width: 380px;
  }
  .contact__name {
    font-weight: 700;
    font-size: 27px;
    color: var(--accent);
    margin-bottom: 14px;
  }
  .contact__rule {
    width: 150px;
    height: 1px;
    background: var(--rule);
    margin: 10px 0;
  }
  .contact__line {
    font-size: 19px;
    line-height: 1.3;
  }
  .contact__phones {
    font-size: 19px;
    margin-top: 6px;
  }
  .contact__label {
    font-weight: 700;
    color: var(--accent);
  }
  .contact__divider { margin: 0 10px; color: var(--text); }
</style>
</head>
<body>
  <section class="card card--front">
    <div class="brand">
      <span class="brand__square"></span>
      <span class="brand__name">KRV</span>
    </div>
    <p class="tagline">Custom Manufacture Any Size or Quantity<br>Fastners for Large Mining Equipment, Trains,<br>Ships, Green Energy Equipment<br>or Government Projects</p>
    <div class="card__band"></div>
  </section>

  <section class="card card--back">
    <h1 class="contact__name">Lic. Mariela Ortega Vidal</h1>
    <div class="contact__rule"></div>
    <p class="contact__line">Cotizaciones en<br>ventas.krv@tornimail.com</p>
    <div class="contact__rule"></div>
    <p class="contact__phones">
      <span class="contact__label">P:</span> 8710004512
      <span class="contact__divider">|</span>
      <span class="contact__label">M:</span> 8710009835
    </p>
    <div class="card__band"></div>
  </section>
</body>
</html>
```